Harbor Lanterns Book Cover Design

Book Cover Design Brief:
Title: Harbor Lanterns
Author: Dena Morrow
đź§­ Subtitle:
A Handbook for the Woman in the Storm or Set to Begin
🎯 Badge Text:
A Compass for Women Navigating Transformation
Trim Size: 6 x 9 inches
Total Number of Pages: Estimate 204 pages (including front/back matter and section dividers).
⸻

đź§­ Overview

Harbor Lanterns is a powerful, faith-based guide and story collection written by Dena Morrow who shares stories of 12 other women. Each chapter offers real-life insight and encouragement for women walking through the emotional wilderness of life—divorce, grief, burnout, identity shifts, loss, and uncertainty. This book isn’t about being lost in nature—it’s about navigating the unseen wilderness of the heart and soul, and finding sacred direction through faith, sisterhood, and intentional self-discovery. It’s for the woman who feels alone in what she’s going through, and is ready to rise again—with strength, clarity, and support.
đź§­ The Compass Framework
The book is grounded in Dena Morrow’s Compass Framework: Community, Openness, Mindset, Purposeful Movement, Accountability, Support, and Self-Care. This 7-part model guides readers from feeling lost to finding purpose, and the compass symbol should appear on the cover as a subtle but meaningful visual representing that inner journey.
🎨 Design Direction Must Haves
• A single woman in a wilderness-like setting (open field, mist, shoreline, etc.), visually representing emotional solitude and personal reflection • A compass or symbolic directional element integrated into the design (can be subtle—part of the background, light, path, etc.) •Mood should reflect quiet strength, inner transformation, hope and sacred guidance
Color palette: Deep greens, earthy tones, and warm golden or divine light—evoking grounding, hope, and spiritual depth
Title: Harbor Lanterns
• “Wilderness” in a natural, elegant font (same as The Harbor Lantern logo if possible) “Wisdom” in a bold serif to evoke strength and maturity
đź§­ Subtitle:
Author Name: Dena Morrow (centered or lower third, clean serif font)
Badge Text: 🎯 Badge Text:
(discreet, bottom right or near author name—no drop shadows)

Nice to Haves: Subtle visual cues of sisterhood or support in the distance (faint outlines, footsteps, horizon silhouettes) • Divine light or glow to represent God’s presence • Natural textures like breeze, water, or mist to evoke movement and transition •A sense of forward momentum—even if the woman is standing still
Should Not Have •Literal forest survival imagery •Cold or overly corporate fonts •Harsh primary colors or visual clutter
Back Cover / Spine Note The design should flow naturally into the spine and back cover. The compass and wilderness elements should feel part of the world, not placed on top of it.
Back Cover Description:
Harbor Lanterns is a healing guide and collection of real stories from women who have walked through life’s hardest seasons. Divorce, grief, abandonment, illness, burnout, addiction, estrangement, narcissistic abuse, homelessness, and the loss of loved ones are all part of the emotional wilderness this book speaks to.
If you feel lost, stuck, or unsure of who you are now, you are not alone. This book is for the woman standing in the middle of her wilderness, ready to take the next step toward healing and purpose.
Each chapter offers real truth and practical encouragement, with reflections that point you back to your strength, your True North, and the life you were made for.
Harbor Lanterns helps you reclaim faith, power, and purpose through the Compass Framework, a path shaped by values like community, mindset, and self-care.
Harbor Lanterns is a healing guide and collection of real stories from women who have walked through life’s hardest seasons. Written by life and business coach Dena Morrow, the book shares her personal journey alongside the voices of 12 courageous women. Divorce, grief, abandonment, illness, burnout, addiction, estrangement, narcissistic abuse, homelessness, and the loss of loved ones are all part of the emotional wilderness this book speaks to.

Whether you are standing in the fire or ready to rise from it, this book was written to meet you there. It is for the woman who feels stuck, shaken, or unsure of who she is now and knows something within her is ready to heal.

Each chapter offers truth and encouragement, with reflections that point you back to your strength, your True North, and the life you were made for.

With every page, you are reminded that you are not lost. You are finding your way as you engage with Dena’s story, the experiences of 12 other women, apply the tools, and move forward with clarity and courage.

Author Bio:
Dena Morrow is a life and business coach, speaker, and author who empowers women to reclaim their faith, power, and purpose after life has shaken their foundation. As the founder of The Harbor Lantern, she helps women move forward with clarity and confidence through seasons of change, loss, and transformation.

Through her coaching, workshops, and writing, Dena creates spaces where women stop feeling stuck and start rising, equipped with tools, community, and a renewed sense of direction for the life ahead.

Target Market(s)

Women ages 30-80

Industry/Entity Type

Faith Based Self Help, Spiritual Growth • Christian Living / Women’s Issues • Faith-Based Personal Development • Self-Help / Spiritual • Women’s Empowerment • Personal Transformation

Font styles to use
Serif
Sans Serif

Requirements
Must have
• A cover that visually reflects the emotional wilderness women experience during life transitions—grief, divorce, abandonment, identity loss, loss of loved one, estrangement, addiction, burnout, etc.—and the sacred path toward hope, strength, and purpose • A design that communicates both solitude and resilience, with visual cues that suggest faith, guidance, and transformation • A compass symbol or directional element subtly integrated to represent the Compass Framework (Community, Openness, Mindset, Purposeful Movement, Accountability, Support, Self-Care) • The overall tone should be inspiring, reflective, and spiritually grounded—not clinical, overly modern, or corporate • Designers are encouraged to explore concepts involving a single woman or symbolic imagery that evokes personal journey and inner navigation • Use of natural elements (landscape, light, sky, mist, etc.) is welcomed but not required—designers may propose abstract, minimalist, or layered concepts that align with the book’s message • Include the following text: • Title: Harbor Lanterns • Subtitle: đź§­ Subtitle: A Handbook for the Woman in the Storm or Set to Begin 🎯 Badge Text: A Compass for Women Navigating Transformation • Author: Dena Morrow •If you are using women they need to be real, diverse in age between 30-80 , body type and demographics
Nice to have
• A woman (or symbolic figure) in the design to reflect the personal, emotional journey of transformation • Subtle visual references to faith, sisterhood, or unseen support (e.g., faint silhouettes, glowing light, soft horizon figures, or abstract representations) • Creative use of natural elements like fog, water, paths, or sky to symbolize movement, mystery, or healing • A warm, layered color palette that transitions from darkness or shadow into light—suggesting hope and divine guidance • Textured or painterly backgrounds that feel organic and timeless • Compass elements woven into the environment (not pasted on top)—integrated as part of the visual metaphor • A sense of emotional depth or quiet strength that draws the viewer in • A design that would appeal to a wide age range of women (not too youthful or too somber)
Should not have
• Literal or clichĂ© wilderness imagery that feels like survival gear, camping, or rugged outdoor adventure • Harsh or neon colors, overly bright palettes, or anything that feels “salesy” or corporate • Clip art, cartoon-style illustrations, or flat graphics that lack emotional depth • Fonts that are overly modern, decorative, or hard to read—especially script fonts that look informal or casual • Designs that feel cold, sterile, masculine, or tech-driven • Cluttered layouts or elements that distract from the core message of faith, reflection, and transformation • Any portrayal that makes the woman look hopeless or abandoned—this is a story of resilience and rising, not despair. • A “sorority” or exclusive club feel—this book should never appear as if it’s only for a select group or the “cool girls” • Any design that suggests perfection, status, or elitism—this is about raw, real life, and inner healing • Glamour-focused imagery that disconnects from authenticity or emotional depth

```html
<!DOCTYPE html>
<html lang="en">
<head>
<meta charset="utf-8">
<title>Harbor Lanterns — Full Cover Wrap</title>
<link href="https://fonts.googleapis.com/css2?family=Parisienne&family=Libre+Baskerville:wght@400;700&family=Alegreya:ital@1&family=Kurale&family=Roboto:wght@400&display=swap" rel="stylesheet">
<style>
  :root {
    --page: #ffffff;
    --ink-dark: #1f1c10;
    --ink-light: #ffffff;
    --sky-olive: #8a8749;
    --sky-gold: #d9c463;
    --glow: #fff6c8;
    --field-brown: #4a3b1c;
    --back-top: #6f6f45;
    --back-mid: #8b7d3f;
    --back-bottom: #3e3018;
    --spine-top: #e9e7e0;
    --spine-bottom: #cfcbc1;
    --portrait: #c99a35;
    --badge-fill: #f7f5ef;
    --badge-ring: #8c8361;
  }
  * { margin: 0; padding: 0; box-sizing: border-box; }
  html, body { width: 1200px; height: 1200px; overflow: hidden; background: var(--page); }

  .wrap { position: absolute; left: 47.5px; top: 206px; width: 1112.5px; height: 795px; }

  /* Back cover */
  .back-cover {
    position: absolute; left: 0; top: 0; width: 530px; height: 795px;
    background:
      radial-gradient(ellipse 70% 30% at 55% 12%, rgba(230,215,140,.45), transparent 70%),
      linear-gradient(180deg, var(--back-top) 0%, var(--back-mid) 55%, var(--back-bottom) 100%);
    color: var(--ink-light);
  }
  .back-title { position: absolute; left: 0; width: 530px; top: 20px; text-align: center; line-height: 1; font-weight: 400; }
  .back-title .script { display: block; font-family: "Parisienne", cursive; font-size: 78px; }
  .back-title .serif { display: block; font-family: "Libre Baskerville", serif; font-size: 58px; margin-top: -6px; }

  .blurb { position: absolute; left: 33px; top: 153px; width: 464px;
    font-family: "Roboto", sans-serif; font-size: 12.4px; line-height: 17.2px; text-align: justify; }
  .blurb p + p { margin-top: 17px; }

  .portrait { position: absolute; left: 33px; top: 481px; width: 151px; height: 176px; background: linear-gradient(180deg,#f4f1ec 0%, #f4f1ec 45%, var(--portrait) 100%); }
  .author-back { position: absolute; left: 199px; top: 476px; font-family: "Libre Baskerville", serif; font-weight: 400; font-size: 28px; letter-spacing: 4px; }
  .bio { position: absolute; left: 199px; top: 517px; width: 298px;
    font-family: "Roboto", sans-serif; font-size: 11.8px; line-height: 17.2px; text-align: justify; }

  .imprint { position: absolute; left: 33px; top: 706px; font-family: "Libre Baskerville", serif; font-weight: 400; color: var(--ink-light); line-height: 1; }
  .imprint .small { display: block; font-size: 10px; letter-spacing: 3px; margin-left: 62px; }
  .imprint .large { display: block; font-size: 30px; letter-spacing: 1px; margin-top: 4px; }

  /* Spine */
  .spine { position: absolute; left: 530px; top: 0; width: 52.5px; height: 795px; overflow: hidden;
    background: linear-gradient(180deg, var(--spine-top), var(--spine-bottom)); color: var(--ink-dark); }
  .spine-text { position: absolute; left: 50%; top: 28px; transform-origin: 0 0;
    transform: rotate(90deg) translateY(-50%); white-space: nowrap; line-height: 1; display: flex; align-items: baseline; gap: 12px; }
  .spine-text .script { font-family: "Parisienne", cursive; font-size: 50px; }
  .spine-text .serif { font-family: "Libre Baskerville", serif; font-size: 44px; }
  .spine-author { position: absolute; left: 50%; top: 590px; transform-origin: 0 0;
    transform: rotate(90deg) translateY(-50%); white-space: nowrap; line-height: 1;
    font-family: "Libre Baskerville", serif; font-size: 24px; letter-spacing: 1px; }

  /* Front cover */
  .front-cover { position: absolute; left: 582.5px; top: 0; width: 530px; height: 795px; overflow: hidden; }
  .front-scene { position: absolute; inset: 0;
    background:
      radial-gradient(circle at 51% 35%, var(--glow) 0%, rgba(255,240,170,.85) 8%, rgba(220,200,100,.4) 28%, transparent 55%),
      linear-gradient(180deg, var(--sky-olive) 0%, var(--sky-gold) 45%, #c9b560 62%, #8f7a3a 80%, var(--field-brown) 100%); }
  .front-title { position: absolute; left: 0; width: 530px; top: 28px; text-align: center; line-height: 1; font-weight: 400; }
  .front-title .script { display: block; font-family: "Parisienne", cursive; font-size: 112px; color: var(--ink-light); }
  .front-title .serif { display: block; font-family: "Libre Baskerville", serif; font-weight: 700; font-size: 84px; color: var(--ink-dark); margin-top: -14px; }
  .subtitle { position: absolute; left: 20px; width: 490px; top: 320px; text-align: center;
    font-family: "Alegreya", serif; font-style: italic; font-size: 26px; line-height: 35px; color: var(--ink-dark); }
  .badge { position: absolute; left: 31px; top: 535px; width: 150px; height: 150px; border-radius: 50%;
    background: var(--badge-fill); border: 2px solid var(--badge-fill); box-shadow: inset 0 0 0 4px var(--badge-fill), inset 0 0 0 5.5px var(--badge-ring);
    display: flex; align-items: center; justify-content: center; text-align: center;
    font-family: "Kurale", serif; font-size: 14.5px; line-height: 22px; letter-spacing: 1px; color: var(--ink-dark); }
  .author-front { position: absolute; left: 0; width: 530px; top: 733px; text-align: center;
    font-family: "Libre Baskerville", serif; font-size: 38px; letter-spacing: 5px; color: var(--ink-light); }
</style>
</head>
<body>
<div class="wrap">
  <section class="back-cover">
    <h2 class="back-title"><span class="script">Harbor</span><span class="serif">Lanterns</span></h2>
    <div class="blurb">
      <p>Harbor Lanterns is a healing guide and collection of real stories from women who have walked through life’s hardest seasons. Divorce, grief, abandonment, illness, burnout, addiction, estrangement, narcissistic abuse, homelessness, and the loss of loved ones are all part of the emotional wilderness this book speaks to.</p>
      <p>If you feel lost, stuck, or unsure of who you are now, you are not alone. This book is for the woman standing in the middle of her wilderness, ready to take the next step toward healing and purpose.</p>
      <p>Each chapter offers real truth and practical encouragement, with reflections that point you back to your strength, your True North, and the life you were made for.</p>
      <p>Harbor Lanterns helps you reclaim faith, power, and purpose through the Compass Framework, a path shaped by values like community, mindset, and self-care.</p>
      <p>With every page, you are reminded that you are not lost. You are finding your way as you engage with the stories, apply the tools, and move forward with clarity and courage.</p>
    </div>
    <div class="portrait" role="img" aria-label="Author portrait photo of Dena Morrow"></div>
    <h3 class="author-back">Dena Morrow</h3>
    <p class="bio">Lorem ipsum dolor sit amet, consectetur adipiscing elit, sed do eiusmod tempor incididunt ut labore et dolore magna aliqua. Quis ipsum suspendisse ultrices gravida. Risus commodo viverra maecenas accumsan lacus vel facilisis. Lorem ipsum dolor sit amet, consectetur adipiscing elit, sed do eiusmod tempor incididunt ut labore et dolore magna aliqua. Quis ipsum suspendisse ultrices gravida.</p>
    <div class="imprint"><span class="small">THE HARBOR</span><span class="large">LANTERN</span></div>
  </section>

  <section class="spine">
    <div class="spine-text"><span class="script">Harbor</span><span class="serif">Lanterns</span></div>
    <div class="spine-author">Dena Morrow</div>
  </section>

  <section class="front-cover">
    <div class="front-scene" role="img" aria-label="Golden misty meadow at sunrise with a woman in a pale dress walking away toward a glowing compass-star sun over distant hills"></div>
    <h1 class="front-title"><span class="script">Harbor</span><span class="serif">Lanterns</span></h1>
    <p class="subtitle">A Compass for Finding Faith &amp; Strength When<br>Life Changes</p>
    <div class="badge"><p>A Guide<br>for Women<br>Navigating<br>Transformation</p></div>
    <p class="author-front">Dena Morrow</p>
  </section>
</div>
</body>
</html>
```